We need packaging box design for our solar lights

We need a design for our solar string lights packaging boxes. The final design should communicate an added enjoyment, comfort and beauty when our lights are used to light up warm evening nights in places like backyard, patio restaurant or even family event.

Front and back side of box can be more visual while sides can be used for technical information about the product. There are 2 types of boxes which will have same design - except they need to indicate difference in # of bulbs 10 or 16 . also size of 16 bulb product box is slightly larger so design will need to be slightly adjusted.

Our original logo needs to have "Meadowglow Lamps" text added to it as well.

We put all together in the attachment with some of the examples of photos we like.

Below are more attached files:
1st attachment - general info and samples of photos
Second attachments are photos of our product - they can be adjusted/photoshoped in any way you wish to make the design - or any other acceptable photos you create can be used
Third set of attachments are box templates for 10 and 16 bulbs size box
last are files for logo - choose any you like, edit any colors / text needs to be added/changed to "Meadowglow Lamps " - not go with meadowglow

Target Market(s)

People with yards, patios, restaurants, wedding places... any celebrations or just relaxing during nice warm evening in the beautifully lit place...

Colors

Designer to choose colors to be used in the design.

Requirements
Must have
• indication of bulb numbers
• logo and name Meadowglow lamps
• rest is up to creativity of designer
Nice to have
• some icons

```html
<!DOCTYPE html>
<html lang="en">
<head>
<meta charset="utf-8">
<title>Meadowglow Lamps – Solar String Lights Box Dieline</title>
<link rel="stylesheet" href="https://fonts.googleapis.com/css2?family=Oswald:wght@700&family=Roboto+Slab:wght@700&family=Arimo:wght@400;700&display=swap">
<style>
  :root{
    --paper:#ffffff;
    --frame:#1a1a1a;
    --flap:#333333;
    --panel:#050505;
    --cream:#f6f0b8;
    --gold:#c9a25a;
    --gold-light:#f2dfae;
    --amber:#e08a2c;
    --green:#1f9e1f;
    --lime:#86e01a;
    --orange:#ff8a1e;
    --white:#ffffff;
  }
  html,body{margin:0;padding:0;overflow:hidden;background:var(--paper);}
  .canvas{position:relative;width:1094px;height:1200px;overflow:hidden;background:var(--paper);}
  .dieline{position:absolute;inset:0;width:1094px;height:1200px;}
  .brand-title{position:absolute;left:58px;top:434px;width:270px;text-align:center;margin:0;white-space:nowrap;}
  .brand-title__name{display:block;font-family:"Oswald",sans-serif;font-weight:700;font-size:36px;line-height:44px;letter-spacing:1px;
    background:linear-gradient(180deg,var(--white) 0%,var(--gold-light) 45%,var(--gold) 100%);-webkit-background-clip:text;background-clip:text;color:transparent;}
  .brand-title__sub{display:block;font-family:"Roboto Slab",serif;font-weight:700;font-size:34px;line-height:40px;color:var(--white);text-shadow:0 0 10px rgba(255,255,255,.45);}
  .bulb-badge{position:absolute;left:152px;top:551px;width:74px;height:88px;box-sizing:border-box;border:3px solid var(--gold-light);border-radius:14px;
    background:linear-gradient(180deg,#3a2a12,#8a6a2c 55%,#3a2a12);display:flex;flex-direction:column;align-items:center;justify-content:center;
    box-shadow:0 0 0 2px #000,0 0 0 3px var(--gold);text-align:center;color:var(--white);font-family:"Oswald",sans-serif;font-weight:700;}
  .bulb-badge__count{font-size:30px;line-height:30px;}
  .bulb-badge__unit{font-size:13px;line-height:14px;}
  .bulb-badge__kind{font-size:7px;line-height:8px;font-family:"Arimo",sans-serif;}
  .brand-mark{position:absolute;left:508px;top:446px;width:80px;display:flex;align-items:center;gap:4px;font-family:"Arimo",sans-serif;font-weight:700;font-size:9px;color:var(--white);white-space:nowrap;}
  .brand-mark__dot{width:8px;height:8px;border-radius:50%;background:var(--orange);flex:none;}
  .info{position:absolute;left:662px;top:476px;width:320px;font-family:"Arimo",sans-serif;font-weight:700;}
  .info__heading{margin:0 0 2px 3px;font-size:9px;line-height:12px;color:var(--lime);}
  .info__text{margin:0 0 16px 0;font-size:7.5px;line-height:14.5px;color:var(--orange);}
</style>
</head>
<body>
<div class="canvas">
  <svg class="dieline" viewBox="0 0 848 929" xmlns="http://www.w3.org/2000/svg">
    <defs>
      <radialGradient id="frontGlow" cx="0.55" cy="1" r="0.8">
        <stop offset="0" stop-color="#7a4a18"/>
        <stop offset="0.45" stop-color="#2a1a0a"/>
        <stop offset="1" stop-color="#050505"/>
      </radialGradient>
      <linearGradient id="photoWarm" x1="0" y1="0" x2="0" y2="1">
        <stop offset="0" stop-color="#2c2a22"/>
        <stop offset="0.6" stop-color="#6b5230"/>
        <stop offset="1" stop-color="#1c150c"/>
      </linearGradient>
      <linearGradient id="backWave" x1="0" y1="0" x2="1" y2="0">
        <stop offset="0" stop-color="#c8713a"/>
        <stop offset="0.5" stop-color="#8a4a25"/>
        <stop offset="1" stop-color="#f0a060"/>
      </linearGradient>
      <radialGradient id="backGlow" cx="0.75" cy="0.3" r="0.6">
        <stop offset="0" stop-color="#3a2a22"/>
        <stop offset="1" stop-color="#050505"/>
      </radialGradient>
    </defs>

    <rect class="sheet-frame" x="2" y="2" width="844" height="925" fill="none" stroke="var(--frame)" stroke-width="2"/>

    <path class="flap flap--top" d="M460 312 L506 150 Q512 130 535 130 L810 130 L810 300 L816 312 Z" fill="var(--flap)"/>
    <path class="flap flap--bottom-front" d="M33 577 L460 577 L355 748 L355 800 L145 800 L145 748 Z" fill="var(--flap)"/>
    <path class="flap flap--bottom-back" d="M460 577 L816 577 L637 748 L637 800 L460 800 Z" fill="var(--flap)"/>
    <line x1="460" y1="577" x2="460" y2="800" stroke="#fff" stroke-width="1"/>

    <rect class="panel-front" x="33" y="312" width="427" height="265" fill="url(#frontGlow)" role="img" aria-label="Night garden scene warmly lit by string lights"/>
    <rect class="panel-back" x="460" y="312" width="356" height="265" fill="url(#backGlow)"/>
    <path class="back-wave" d="M460 560 C540 520 600 545 680 540 C740 536 790 525 816 535 L816 577 L460 577 Z" fill="url(#backWave)" opacity="0.85"/>
    <path d="M460 548 C560 510 640 560 816 528" fill="none" stroke="#f3c59a" stroke-width="1" opacity="0.7"/>

    <g class="photo-hexes" stroke="var(--cream)" stroke-width="4">
      <polygon points="327,343 372,369 372,419 327,445 282,419 282,369" fill="url(#photoWarm)" role="img" aria-label="House terrace with string lights at night"/>
      <polygon points="273,440 318,466 318,516 273,542 228,516 228,466" fill="url(#photoWarm)" role="img" aria-label="Close-up of a glowing bulb"/>
      <polygon points="383,440 428,466 428,516 383,542 338,516 338,466" fill="url(#photoWarm)" role="img" aria-label="Garden wall lit by warm bulbs"/>
    </g>

    <g class="feature-icons" font-family="Arimo, sans-serif" font-size="3.6" fill="#fff" text-anchor="middle">
      <circle cx="101" cy="536" r="17" fill="var(--green)"/>
      <circle cx="101" cy="530" r="4" fill="#fff"/>
      <g stroke="#fff" stroke-width="1"><line x1="101" y1="522" x2="101" y2="524"/><line x1="93" y1="530" x2="95" y2="530"/><line x1="107" y1="530" x2="109" y2="530"/></g>
      <text x="101" y="541">charges during</text><text x="101" y="545">the day</text>
      <circle cx="144" cy="536" r="17" fill="var(--green)"/>
      <path d="M146 523 A7 7 0 1 0 150 533 A5.5 5.5 0 1 1 146 523 Z" fill="#fff"/>
      <text x="144" y="544">lights at dusk</text>
      <circle cx="186" cy="536" r="17" fill="var(--green)"/>
      <path d="M186 537 L186 527 M186 531 C181 530 180 526 181 523 C185 524 187 527 186 531 M186 530 C190 528 192 525 191 522 C188 523 186 526 186 530" stroke="#fff" stroke-width="1.2" fill="none"/>
      <text x="186" y="544">clean energy</text>
    </g>
  </svg>

  <h1 class="brand-title">
    <span class="brand-title__name">MEADOWGLOW</span>
    <span class="brand-title__sub">Lamps</span>
  </h1>

  <div class="bulb-badge">
    <span class="bulb-badge__count">16</span>
    <span class="bulb-badge__unit">BULBS</span>
    <span class="bulb-badge__kind">SOLAR STRING<br>LIGHTS</span>
  </div>

  <div class="brand-mark"><span class="brand-mark__dot"></span>meadowglow</div>

  <div class="info">
    <h2 class="info__heading">How the Solar Light work:</h2>
    <p class="info__text">The solar light has a solar panel that converts sunlight into electricity which is stored during the day in the rechargeable batteries. At night, the solar light uses stored energy to light up. The operating time depends on the geographical location, season and daily weather condition.</p>
    <h2 class="info__heading">Where to place solar panel:</h2>
    <p class="info__text">For maximum effectiveness place the solar panel in the location with full, direct sunlight.</p>
    <h2 class="info__heading">How To Install Solar Pane</h2>
    <p class="info__text">Earth Spike: simply insert the ground stake (included ) into the ground until it is firmly in place.<br>Wall Mount: simply mount the solar panel onto the wall with two screws (included ) and adjust the angle of solar panel for maximum sun exposure.</p>
  </div>
</div>
</body>
</html>
```